Personal Web page for recruiter and owner of consulting firm

I work full time as a recruiter so I want a page that allows for me to support my efforts. I would like a long single page, I need to be able to upload four two minute videos, and 4 images. I also want the color scheme to match with my consulting company. I own the domain marcusfenwold.net already through wordpress . I took a shot at it myself and its terrible.

Target Market(s)

Potential clients

Industry/Entity Type

Management Consulting

Logo Text

marcus fenwold

Font styles to use
Serif

Requirements
Must have
• Must in color scheme go well with my consulting company logo attached
• Must be able to upload 4 two minute videos and 4 images (photos of me)
• Single long scroll page
• Modern and clean
Nice to have
• Easy for me to update videos images and text without complex coding
Should not have
• I want the design and feel to go well with my logos not exactly replicate it

```html
<!DOCTYPE html>
<html lang="en">
<head>
<meta charset="utf-8">
<title>Fenwold Strategies</title>
<link href="https://fonts.googleapis.com/css2?family=Lato:wght@400;700;900&family=Open+Sans:wght@400;600;700&family=Oswald:wght@500;600&display=swap" rel="stylesheet">
<style>
:root{
  --navy:#0b2e5c;
  --navy-deep:#0a2548;
  --sky:#6aaee0;
  --sky-soft:#7db8e6;
  --ink:#1b1b1b;
  --text:#444;
  --charcoal:#2b2b2b;
  --footer:#262626;
  --line:#cfcfcf;
  --white:#fff;
}
*{box-sizing:border-box;margin:0;padding:0}
html,body{width:1200px;height:3822px;overflow:hidden}
body{position:relative;background:var(--white);font-family:"Open Sans",Arial,sans-serif;color:var(--text)}
.abs{position:absolute}
.center{text-align:center}

/* header */
.site-header{left:0;top:0;width:1200px;height:107px;background:var(--white)}
.brand{left:97px;top:36px;display:flex;align-items:center;gap:12px;color:#333;font-family:"Open Sans",Arial,sans-serif;font-weight:600;font-size:26px;line-height:1}
.brand-mark{width:22px;height:22px;background:var(--navy)}
.contact-item{top:22px;display:flex;gap:12px;align-items:center;font-size:15px;color:#222;line-height:1.45}
.contact-item strong{display:block;font-weight:700;color:var(--navy)}
.contact-item svg{flex:none}

/* nav */
.main-nav{left:0;top:107px;width:1200px;height:56px;background:var(--navy)}
.main-nav ul{list-style:none;position:relative;height:56px}
.main-nav li{position:absolute;top:0;height:56px;line-height:56px;color:var(--white);font-family:Lato,Arial,sans-serif;font-weight:700;font-size:14px;text-align:center}
.main-nav li.active{background:var(--sky)}

/* hero */
.hero{left:0;top:163px;width:1200px;height:515px;background:linear-gradient(100deg,#3d6e78 0%,#2e6b76 30%,#2a6571 60%,#3a7682 100%)}
.hero-photo{left:0;top:0;width:300px;height:515px;background:linear-gradient(90deg,#3a3d42,#5b6068 70%,#44484f)}
.hero-title{left:318px;top:120px;color:var(--white);font-family:Oswald,Arial,sans-serif;font-weight:600;line-height:1.15}
.hero-title .big{display:block;font-size:58px;letter-spacing:2px}
.hero-title .mid{display:block;font-size:36px;letter-spacing:1px;margin-top:12px}
.hero-lead{left:318px;top:285px;color:var(--white);font-weight:600;font-size:18px}
.hero-arrows{left:318px;top:348px}
.search-box{left:793px;top:65px;width:309px;height:385px;background:var(--white);padding:22px 15px}
.search-box h2{font-family:Lato,Arial,sans-serif;font-weight:700;font-size:19px;color:var(--navy);text-align:center;margin-bottom:30px}
.field{display:block;width:280px;height:39px;border:1px solid #555;margin-bottom:11px;padding:0 10px;font-size:14px;line-height:37px;color:#333}
.btn-navy{background:var(--navy);color:var(--white);font-weight:700;font-size:14px;text-align:center}
.search-box .btn-navy{width:150px;height:45px;line-height:45px;margin-top:26px}

/* tagline band */
.tag-band{left:0;top:678px;width:1200px;height:131px;background:var(--charcoal);color:var(--white);text-align:center}
.tag-band h2{font-family:Lato,Arial,sans-serif;font-weight:700;font-size:29px;margin-top:31px}
.tag-band p{font-weight:600;font-size:16px;margin-top:12px}

/* section headings */
.section-title{left:0;width:1200px;text-align:center;font-family:Lato,Arial,sans-serif;font-weight:700;font-size:26px;color:var(--navy)}
.rule{left:520px;width:160px;height:3px;background:var(--navy)}

/* intro cards */
.card{top:993px;width:484px;height:362px;border:1px solid #d8d8d8;border-radius:4px;overflow:hidden}
.card-head{height:57px;background:var(--sky);color:var(--white);font-family:Lato,Arial,sans-serif;font-weight:700;font-size:21px;display:flex;align-items:center;justify-content:center;gap:12px}
.card-body{height:305px;padding:40px 40px 0;text-align:center;font-size:13px;line-height:1.6}
.card.dark .card-body{background:linear-gradient(160deg,#2a2623,#171513 60%,#221e1a);color:var(--white)}
.card .more{display:block;margin-top:20px;font-weight:700;font-size:15px}
.card.light .more{color:var(--sky);font-weight:600}
.card-actions{display:flex;justify-content:center;gap:10px;margin-top:48px}
.btn-sky{width:120px;height:42px;line-height:42px;background:var(--sky);color:var(--white);font-weight:600;font-size:15px}
.btn-outline{width:145px;height:42px;line-height:40px;border:2px solid #333;background:var(--white);color:#222;font-weight:600;font-size:15px}

/* video panels */
.video-panel{width:600px;height:405px;color:var(--white);text-align:center}
.video-panel.navy{background:linear-gradient(135deg,#0e3566,#0a2a52)}
.video-panel.sky{background:linear-gradient(135deg,#7bb7e4,#5da3da)}
.video-panel svg{display:block;margin:64px auto 0}
.video-panel h3{font-family:Lato,Arial,sans-serif;font-weight:700;font-size:23px;margin-top:44px}
.video-panel p{font-size:14px;line-height:1.85;width:560px;margin:30px auto 0}

/* blog */
.post{top:2030px;width:318px;text-align:center}
.post-photo{position:relative;width:318px;height:227px}
.date{position:absolute;left:0;bottom:0;width:60px;height:62px;background:#333;color:var(--white);font-weight:700;font-size:15px;line-height:1.25;padding-top:10px}
.post h3{font-weight:600;font-size:19px;color:#222;margin-top:26px}
.post p{font-size:13px;line-height:1.6;margin:16px 10px 0}
.post .read{display:inline-block;width:108px;height:41px;line-height:37px;margin-top:26px;font-weight:700;font-size:14px;border:2px solid #333;color:#222}
.post .read.filled{background:var(--navy);border-color:var(--navy);color:var(--white)}

/* contact form */
.form-field{height:47px;border:1px solid #555;padding:0 12px;line-height:45px;font-size:14px;color:#333}
.form-btn{left:528px;top:3353px;width:145px;height:46px;line-height:46px}

/* footer */
.site-footer{left:0;top:3480px;width:1200px;height:342px;background:var(--footer);color:var(--white)}
.footer-brand{left:0;top:70px;width:1200px;display:flex;justify-content:center;align-items:center;gap:12px;font-family:"Open Sans",Arial,sans-serif;font-weight:600;font-size:26px;line-height:1;color:var(--white)}
.footer-brand .brand-mark{background:var(--white)}
.footer-nav{left:0;top:187px;width:1200px;text-align:center;font-family:Lato,Arial,sans-serif;font-weight:700;font-size:16px;word-spacing:2px}
.footer-nav span.sep{margin:0 18px;font-weight:400}
.footer-rule{left:99px;top:240px;width:1002px;height:1px;background:#8a8a8a}
.copyright{left:99px;top:289px;font-size:13px;font-weight:700}
.social{left:910px;top:279px;display:flex;gap:9px}
.social span{width:36px;height:36px;border:2px solid var(--white);border-radius:50%}
</style>
</head>
<body>

<header class="abs site-header">
  <div class="abs brand"><span class="brand-mark"></span>Fenwold Strategies</div>
  <div class="abs contact-item" style="left:693px">
    <svg width="34" height="34" viewBox="0 0 34 34"><circle cx="17" cy="17" r="15" fill="none" stroke="#333" stroke-width="2"/><rect x="10" y="12" width="14" height="10" fill="none" stroke="#333" stroke-width="1.8"/><path d="M10 12l7 6 7-6" fill="none" stroke="#333" stroke-width="1.8"/></svg>
    <div>Mail Us!<strong>info@marcusfenwold.net</strong></div>
  </div>
  <div class="abs contact-item" style="left:932px">
    <svg width="34" height="34" viewBox="0 0 34 34"><circle cx="17" cy="17" r="15" fill="none" stroke="#333" stroke-width="2"/><path d="M12 10c-2 2-1 6 3 10s8 5 10 3l-3-3-2 1c-2-1-4-3-5-5l1-2z" fill="#333"/></svg>
    <div>Call Us Today!<strong>180 555 0142</strong></div>
  </div>
</header>

<nav class="abs main-nav">
  <ul>
    <li class="active" style="left:99px;width:115px">HOME</li>
    <li style="left:240px;width:120px">RECRUITER</li>
    <li style="left:402px;width:120px">ABOUT US</li>
    <li style="left:565px;width:170px">CONSULTING FIRM</li>
    <li style="left:760px;width:156px">GENERAL SKILLS</li>
    <li style="left:980px;width:136px">CONTACT US</li>
  </ul>
</nav>

<section class="abs hero">
  <div class="abs hero-photo" role="img" aria-label="Photo of a recruiter in a dark suit reaching out for a handshake"></div>
  <h1 class="abs hero-title"><span class="big">FENWOLD</span><span class="mid">STRATEGIES CONSULTING FIRM</span></h1>
  <p class="abs hero-lead">I'm a full time recruiter and own a consulting firm.</p>
  <svg class="abs hero-arrows" width="80" height="44" viewBox="0 0 80 44"><path d="M22 4L6 22l16 18" fill="none" stroke="#fff" stroke-width="3"/><path d="M58 4l16 18-16 18" fill="none" stroke="#fff" stroke-width="3"/></svg>
  <form class="abs search-box">
    <h2>SEARCH JOB WITH US</h2>
    <span class="field">Name</span>
    <span class="field">Company Name</span>
    <span class="field">Direct Phone</span>
    <span class="field">Email</span>
    <div class="btn-navy">SEARCH JOBS</div>
  </form>
</section>

<section class="abs tag-band">
  <h2>Know Who You're Hiring... BEFORE You Hire</h2>
  <p>Get jobs with our recruiter portal</p>
</section>

<h2 class="abs section-title" style="top:877px">WELCOME TO FENWOLD</h2>
<div class="abs rule" style="top:928px"></div>

<article class="abs card dark" style="left:99px">
  <div class="card-head">
    <svg width="18" height="24" viewBox="0 0 18 24"><path d="M9 1a7 7 0 0 0-4 13v4h8v-4A7 7 0 0 0 9 1z" fill="#fff"/><rect x="5" y="19" width="8" height="3" fill="#fff"/></svg>
    Our Recruiters Panel
  </div>
  <div class="card-body" aria-label="Dim office photo behind the panel text">
    Nemo enim ipsam voluptatem quia voluptas sit aspernatur aut odit aut fugit, sed quia consequuntur magni dolores eos qui ratione vo luptatem sequi nesciunt. Neque porro quisquam est, qui dolorem ipsum quia dolor sit amet, consectetur.
    <span class="more">See More &gt;</span>
    <div class="card-actions"><span class="btn-sky">Get Jobs</span><span class="btn-outline">Hire With Us</span></div>
  </div>
</article>

<article class="abs card light" style="left:617px">
  <div class="card-head">
    <svg width="26" height="24" viewBox="0 0 26 24"><circle cx="13" cy="14" r="7" fill="none" stroke="#fff" stroke-width="2"/><path d="M13 1v4M4 5l3 3M22 5l-3 3M1 14h3M22 14h3" stroke="#fff" stroke-width="2"/></svg>
    Our Consulting Firm
  </div>
  <div class="card-body">
    Nemo enim ipsam voluptatem quia voluptas sit aspernatur aut odit aut fugit, sed quia consequuntur magni dolores eos qui ratione vo luptatem sequi nesciunt. Neque porro quisquam est, qui dolorem ipsum quia dolor sit amet, consectetur.
    <span class="more">See More &gt;</span>
    <div class="card-actions"><span class="btn-sky">Get Jobs</span><span class="btn-outline">Hire With Us</span></div>
  </div>
</article>

<section class="abs video-panel navy" style="left:0;top:1441px" aria-label="Mission video panel over a dark blue office photo">
  <svg width="92" height="92" viewBox="0 0 92 92"><circle cx="46" cy="46" r="42" fill="none" stroke="#fff" stroke-width="5"/><path d="M36 28l28 18-28 18z" fill="#fff"/></svg>
  <h3>MISSION</h3>
  <p>Sed ut perspiciatis unde omnis iste natus error sit voluptatem accusantium do loremque laudantium, totam rem aperiam.</p>
</section>
<section class="abs video-panel sky" style="left:600px;top:1441px" aria-label="Team video panel over a light blue workspace photo">
  <svg width="92" height="92" viewBox="0 0 92 92"><circle cx="46" cy="46" r="42" fill="none" stroke="#fff" stroke-width="5"/><path d="M36 28l28 18-28 18z" fill="#fff"/></svg>
  <h3>TEAM</h3>
  <p>Sed ut perspiciatis unde omnis iste natus error sit voluptatem accusantium do loremque laudantium, totam rem aperiam.</p>
</section>

<h2 class="abs section-title" style="top:1926px">OUR BLOG POSTS</h2>
<div class="abs rule" style="top:1975px"></div>

<article class="abs post" style="left:99px">
  <div class="post-photo" role="img" aria-label="Photo of two professionals in a job interview" style="background:linear-gradient(135deg,#c9c2b6,#8f8a84 55%,#4d4f55)"><span class="date">AUG<br>11</span></div>
  <h3>Recruiter Jobs</h3>
  <p>Nemo enim ipsam voluptatem quia voluptas sit asperna tur aut odit aut fugit sed quia consequuntur magni dolores eos ratione.</p>
  <span class="read filled">Read More</span>
</article>
<article class="abs post" style="left:442px">
  <div class="post-photo" role="img" aria-label="Photo of candidates seated in a row waiting for interviews" style="background:linear-gradient(180deg,#3a3a3a,#6f6a66 45%,#b9b5b0)"><span class="date">AUG<br>20</span></div>
  <h3>Consulting Firm</h3>
  <p>Nemo enim ipsam voluptatem quia voluptas sit asperna tur aut odit aut fugit sed quia consequuntur magni dolores eos ratione.</p>
  <span class="read">Read More</span>
</article>
<article class="abs post" style="left:785px">
  <div class="post-photo" role="img" aria-label="Photo of a consultant meeting with a client at a desk" style="background:linear-gradient(135deg,#e8e8e6,#b8b8b8 55%,#3b3f48)"><span class="date">AUG<br>20</span></div>
  <h3>Fenwold Strategies</h3>
  <p>Nemo enim ipsam voluptatem quia voluptas sit asperna tur aut odit aut fugit sed quia consequuntur magni dolores eos ratione.</p>
  <span class="read">Read More</span>
</article>

<section class="abs video-panel sky" style="left:0;top:2544px" aria-label="Recruiter video panel over a light blue desk photo">
  <svg width="92" height="92" viewBox="0 0 92 92"><circle cx="46" cy="46" r="42" fill="none" stroke="#fff" stroke-width="5"/><path d="M36 28l28 18-28 18z" fill="#fff"/></svg>
  <h3>RECRUITER</h3>
  <p>Sed ut perspiciatis unde omnis iste natus error sit voluptatem accusantium do loremque laudantium, totam rem aperiam.</p>
</section>
<section class="abs video-panel navy" style="left:600px;top:2544px" aria-label="Consulting video panel over a dark blue meeting photo">
  <svg width="92" height="92" viewBox="0 0 92 92"><circle cx="46" cy="46" r="42" fill="none" stroke="#fff" stroke-width="5"/><path d="M36 28l28 18-28 18z" fill="#fff"/></svg>
  <h3>CONSULTING</h3>
  <p>Sed ut perspiciatis unde omnis iste natus error sit voluptatem accusantium do loremque laudantium, totam rem aperiam.</p>
</section>

<h2 class="abs section-title" style="top:3024px">GET IN TOUCH WITH US</h2>
<div class="abs rule" style="top:3075px"></div>

<form>
  <span class="abs form-field" style="left:174px;top:3138px;width:414px">Name</span>
  <span class="abs form-field" style="left:612px;top:3138px;width:414px">Email</span>
  <span class="abs form-field" style="left:174px;top:3206px;width:414px">Phone</span>
  <span class="abs form-field" style="left:612px;top:3206px;width:414px">Website</span>
  <span class="abs form-field" style="left:174px;top:3274px;width:852px">Company Name</span>
  <div class="abs btn-navy form-btn">CONTACT US</div>
</form>

<footer class="abs site-footer">
  <div class="abs footer-brand"><span class="brand-mark"></span>Fenwold Strategies</div>
  <div class="abs footer-nav">HOME<span class="sep">|</span>RECRUITER<span class="sep">|</span>ABOUT US<span class="sep">|</span>CONSULTING FIRM<span class="sep">|</span>GENERAL SKILLS<span class="sep">|</span>CONTACT</div>
  <div class="abs footer-rule"></div>
  <p class="abs copyright">© 2017 Fenwold, All Rights Reserved</p>
  <div class="abs social"><span></span><span></span><span></span><span></span><span></span></div>
</footer>

</body>
</html>
```